Harbin Panels Brochure

Harbin Panels New Brochure Brief
Harbin Panels are manufacturers of kitchen and wardrobe doors. We have 2 target markets, one is business to business and the other business to residential customers.
The main message of our business to residential is to inform them that they can give their kitchen or wardrobe a facelift by just replacing doors and save thousands of dollars by doing this partial renovation. However, this is in direct conflict with our business to business customers (kitchen and wardrobe companies) who buy doors from us and sell complete new kitchens and built in wardrobes to the same residential customers.
Please find links to the Harbin Panels brochure and website below for your reference. The current dimensions of the brochure is approx. 21cmH x 29.7cmW. https://harbinpanels.com.au/harbinpanelsbrochure-2/ https://harbinpanels.com.au/
I would like to keep the layout of the brochure internal pages consistent with the current design, however, I am open to your ideas. The orange colour as seen on the front page should be a dominant theme as it’s based on our logo however not too overpowering, I prefer to cover to be white. I would like a new front page design, changing the door photos (they will be shades of white, not coloured) and also delete the words ‘ultimate door collection’. Heading to be along the lines of “Custom made kitchen and wardrobe doors”.
On the internal pages, some new door designs will be added and some deleted. s. We are thinking of changing all the door colours to shades of white but also stating that Harbin Panels can colour match to any major Australian paint brand.
I would like to include a page for Wardrobe Doors with some photos, text and layout options (photo attached). Please add in the before and after images. Please create a before and after using Theo's kitchen in same layout as wardrobe before and after. Please ensure oven is cut from after image. Please add in the photos attached in this brief.
We would also like to include a FAQs section. Some more text describing our product, such as raw material, thickness of doors, painted or unpainted finish and delivery information is to be added.
Re: the ‘edges’ top of page 3; some will be deleted and one new type of edge will be added.
From page 4 onwards, there are different shapes at the bottom of each door design. We are looking for a new way to communicate this as at the moment it is taking up too much room and people do not readily understand that these door patterns can be supplied in the shapes shown in the little diagrams below them.
Please keep in mind all this information will be given at the time of design. I would like to possibly keep the brochure at 8 pages (as it is now). There may be some other changes along the way as this is still in the preliminary stage. Please include the image of our showroom in the brochure mock up.
I look forward to your reply.
Kind Regards,
Marta
* Please note, the images attach with the individual doors need to be changed to some neutral shades such as white, off white, grey, cream etc (similar to the website: https://harbinpanels.com.au/kitchen-doors/)

```html
<!DOCTYPE html>
<html lang="en">
<head>
<meta charset="utf-8">
<title>Harbin Panels – Renovating your kitchen or wardrobe</title>
<link rel="stylesheet" href="https://fonts.googleapis.com/css2?family=Fira+Sans+Condensed:wght@400;700;900&display=swap">
<style>
  :root {
    --orange: #fd9a37;
    --after-red: #f6532d;
    --before-grey: #97a5a8;
    --ink: #111111;
    --paper: #ffffff;
    --before-tone-a: #6b4a2e;
    --before-tone-b: #c79a63;
    --after-tone-a: #d9dfe3;
    --after-tone-b: #8d959b;
  }
  * { box-sizing: border-box; margin: 0; padding: 0; }
  html, body { width: 1200px; height: 848px; overflow: hidden; background: var(--paper); }
  .page {
    position: relative; width: 1200px; height: 848px; overflow: hidden;
    background: var(--paper);
    font-family: "Fira Sans Condensed", "Arial Narrow", sans-serif;
    color: var(--ink);
  }
  .photo { position: absolute; top: 0; height: 559px; }
  .photo--before {
    left: 0; width: 373px;
    background: linear-gradient(160deg, #e8d9b4 0%, var(--before-tone-b) 45%, var(--before-tone-a) 100%);
  }
  .photo--after {
    left: 378px; width: 368px;
    background: linear-gradient(200deg, #f4f6f7 0%, var(--after-tone-a) 50%, var(--after-tone-b) 100%);
  }
  .photo-divider { position: absolute; left: 373px; top: 0; width: 5px; height: 559px; background: var(--paper); }
  .slider-handle { position: absolute; left: 349px; top: 256px; width: 50px; height: 50px; }
  .tag {
    position: absolute; top: 477px; width: 162px; height: 54px;
    display: flex; align-items: center; justify-content: center;
    color: var(--paper); font-family: "Arial", sans-serif; font-size: 23px; letter-spacing: 0.5px;
  }
  .tag--before { left: 0; background: var(--before-grey); }
  .tag--after { left: 584px; background: var(--after-red); }
  .rule { position: absolute; background: var(--orange); }
  .rule--photo-a { left: 0; top: 559px; width: 527px; height: 9px; }
  .rule--photo-b { left: 559px; top: 559px; width: 187px; height: 9px; }
  .rule--foot-a { left: 0; top: 780px; width: 332px; height: 29px; }
  .rule--foot-b { left: 342px; top: 780px; width: 306px; height: 29px; }
  .rule--foot-c { left: 659px; top: 780px; width: 108px; height: 29px; }
  .page-number { position: absolute; left: 22px; top: 780px; line-height: 29px; font-size: 22px; color: var(--ink); }
  .headline { position: absolute; left: 26px; top: 600px; font-weight: 700; text-transform: uppercase; line-height: 1; }
  .headline__line { display: block; font-size: 63px; letter-spacing: 0.5px; }
  .headline__line--second { margin-left: 107px; margin-top: 2px; }
  .headline .accent { color: var(--orange); }
  .info-panel {
    position: absolute; left: 775px; top: 0; width: 393px; height: 848px;
    background: var(--orange);
    padding: 20px 14px 0 24px;
    font-size: 17.2px; line-height: 22.3px; color: var(--ink);
  }
  .info-panel p { margin-bottom: 22px; }
  .info-panel p.contact { margin-top: -4px; }
  .info-panel strong { font-weight: 700; }
</style>
</head>
<body>
<main class="page">
  <div class="photo photo--before" role="img" aria-label="Before: bedroom with dark timber sliding wardrobe doors, unmade bed and clothes on the floor"></div>
  <div class="photo photo--after" role="img" aria-label="After: renovated bedroom with white shaker sliding wardrobe doors, grey bed and striped bedding"></div>
  <div class="photo-divider"></div>
  <svg class="slider-handle" viewBox="0 0 50 50" aria-hidden="true">
    <circle cx="25" cy="25" r="21" fill="none" stroke="#ffffff" stroke-width="4"/>
    <path d="M22 18 L13 25 L22 32 Z" fill="#ffffff"/>
    <path d="M28 18 L37 25 L28 32 Z" fill="#ffffff"/>
  </svg>
  <div class="tag tag--before">BEFORE</div>
  <div class="tag tag--after">AFTER</div>
  <div class="rule rule--photo-a"></div>
  <div class="rule rule--photo-b"></div>

  <h1 class="headline">
    <span class="headline__line">Renovating your</span>
    <span class="headline__line headline__line--second"><span class="accent">Kitchen</span> or <span class="accent">Wardrobe</span></span>
  </h1>

  <div class="rule rule--foot-a"></div>
  <div class="rule rule--foot-b"></div>
  <div class="rule rule--foot-c"></div>
  <span class="page-number">2</span>

  <aside class="info-panel">
    <p><strong>Save time and money.</strong> Competitive prices and the fastest delivery of custom made kitchen and wardrobe doors in Sydney!</p>
    <p><strong>Fast turnaround</strong> Unpainted doors in 5 work&shy;ing days and painted doors in 15 working days – Guaranteed!</p>
    <p><strong>Trade customers:</strong> Cut to size or router only service with pick up and delivery to your premises or painter.</p>
    <p><strong>Huge range of designs.</strong> From plain, contem&shy;porary to shaker style to intricately patterned heritage designs. Flutes, corbels, fretwork, capping moulds, hinges, wardrobe tracks and handles.</p>
    <p><strong>Top quality Australian made material.</strong><br>Doors are made from 18mm white satin moisture resistant (MR) MDF or optionally in 16, 21 or 25mm thickness. All guaranteed to conform to Australian Quality Standards.</p>
    <p><strong>Polyurethane painting</strong>. Doors can be sup&shy;plied painted in polyurethane, with a satin or high gloss finish in the colour of your choice</p>
    <p><strong>Guarantee.</strong> We guarantee the quality and accuracy of all our doors!</p>
    <p class="contact"><strong>Call (02) 9000 4410, fax (02) 9000 4477</strong> or email your door sizes for a quote, trade price list or other information to sales@harbin-panels.com.au.</p>
  </aside>
</main>
</body>
</html>
```